Quillmarsh Property Solutions need a business card design

Hello guys. We would need a business card design asap please.
We are a start up property investment business based in London UK specialised in buying, selling, managing and letting properties and helping distressed property owners.
The name of our Business is Quillmarsh, the logo symbolises the four fundamental elements of the world (earth, air, fire and water) and so it stands for strength, stability, longevity.
We would like the business card to communicate professionalism and reliability. Many many thanks indeed for your work.

Details:

1.) Rosalind Updike
Property Investor
Mobile: +44(0)7700123456
Email: rosalind.quillmarsh@mailbox-example.com

2.) Dominic Updike
Property Investor
Mobile: +44(0)7700987654
Email: dominic.quillmarsh@mailbox-example.com

```html
<!DOCTYPE html>
<html lang="en">
<head>
<meta charset="utf-8">
<title>Quillmarsh Property Solutions – Business Card</title>
<link rel="stylesheet" href="https://fonts.googleapis.com/css2?family=Lato:wght@400;700;900&display=swap">
<style>
  :root {
    --canvas-bg: #e4e5e7;
    --card-white: #fbfbfb;
    --card-black: #151515;
    --ink: #1c1c1c;
    --brand-blue: #2f6fb7;
    --brand-red: #c0272d;
    --brand-green: #1db24a;
    --stripe-blue: #3a64b4;
    --logo-grey: #9a9b9d;
  }
  * { box-sizing: border-box; margin: 0; padding: 0; }
  html, body {
    width: 1200px; height: 926px; overflow: hidden;
    background: var(--canvas-bg);
    font-family: "Lato", Arial, sans-serif;
    color: var(--ink);
  }
  .canvas {
    width: 1200px; height: 926px;
    display: flex; flex-direction: column; align-items: center; justify-content: center;
    gap: 40px;
  }
  .card {
    position: relative;
    width: 700px; height: 400px;
    overflow: hidden;
    box-shadow: 0 6px 18px rgba(0,0,0,0.18);
  }
  .card--front { background: var(--card-white); }
  .card--back { background: var(--card-black); }

  .wave { position: absolute; inset: 0; width: 100%; height: 100%; }

  .brand {
    position: absolute; left: 0; right: 0;
    display: flex; align-items: center; justify-content: center; gap: 10px;
    font-weight: 900; text-transform: uppercase; text-align: center;
  }
  .brand__mark { display: inline-block; flex: none; }
  .brand__name { line-height: 1.05; }
  .brand__name small { display: block; font-size: 0.42em; letter-spacing: 0.08em; }

  .card--front .brand { top: 42px; color: var(--ink); font-size: 25px; letter-spacing: 0.04em; }
  .card--front .brand__mark { width: 22px; height: 22px; background: var(--brand-green); }

  .card--back .brand { top: 150px; color: var(--logo-grey); font-size: 50px; letter-spacing: 0.06em; }
  .card--back .brand__mark { width: 40px; height: 40px; background: var(--logo-grey); }

  .contact { position: absolute; }
  .contact--rosalind { left: 38px; top: 132px; }
  .contact--dominic { left: 352px; top: 190px; }

  .contact__name { font-size: 26px; font-weight: 400; line-height: 1.1; }
  .contact__name strong { font-weight: 700; }
  .contact__role {
    font-size: 14px; color: var(--brand-blue);
    letter-spacing: 0.1em; margin: 2px 0 10px 18px;
  }
  .contact__line { font-size: 14.5px; line-height: 1.5; }
  .contact__line--phone { margin-left: 34px; }
  .contact__line b { font-weight: 700; }
</style>
</head>
<body>
<main class="canvas">

  <section class="card card--front" aria-label="Business card front">
    <svg class="wave" viewBox="0 0 700 400" preserveAspectRatio="none" aria-hidden="true">
      <path fill="var(--stripe-blue)" d="M0,224 C200,316 450,338 700,334 L700,400 L0,400 Z"/>
      <path fill="var(--brand-red)" d="M0,240 C200,322 450,340 700,336 L700,400 L0,400 Z"/>
      <path fill="var(--brand-green)" d="M0,250 C200,336 450,358 700,352 L700,400 L0,400 Z"/>
    </svg>

    <div class="brand">
      <span class="brand__mark"></span>
      <span class="brand__name">Quillmarsh<small>Property Solutions</small></span>
    </div>

    <div class="contact contact--rosalind">
      <p class="contact__name">Rosalind <strong>Updike</strong></p>
      <p class="contact__role">Property Investor</p>
      <p class="contact__line contact__line--phone"><b>m:</b> +44(0)7700123456</p>
      <p class="contact__line"><b>e:</b> rosalind.quillmarsh@mailbox-example.com</p>
    </div>

    <div class="contact contact--dominic">
      <p class="contact__name">Dominic <strong>Updike</strong></p>
      <p class="contact__role">Property Investor</p>
      <p class="contact__line contact__line--phone"><b>m:</b> +44(0)7700987654</p>
      <p class="contact__line"><b>e:</b> dominic.quillmarsh@mailbox-example.com</p>
    </div>
  </section>

  <section class="card card--back" aria-label="Business card back">
    <div class="brand">
      <span class="brand__mark"></span>
      <span class="brand__name">Quillmarsh<small>Property Solutions</small></span>
    </div>
  </section>

</main>
</body>
</html>
```